Business Card Design needed for start up company Halvora

In need of a new business card designed for a start up company based in Sydney, Halvora is a new start up innovative Company, our mission it to make property accessible for everyday Australian and to become the leading Real Estate platform in Australia. We want it to be fresh and clean.

Industry/Entity Type

Financial

Contact Information for Business Card

Section for Name
Section for Title

HALVORA - The Strength of Pooling
Mobile:
Direct:

Font styles to use
Sans Serif

Colors
33a6d7
0692cd
0255a3
ffffff

Requirements
Must have
• Logo, all business card details

```html
<!DOCTYPE html>
<html lang="en">
<head>
<meta charset="utf-8">
<title>Halvora Business Card</title>
<link href="https://fonts.googleapis.com/css2?family=Jost:wght@400;600&display=swap" rel="stylesheet">
<style>
  :root {
    --page-bg: #e4e6ea;
    --navy-deep: #0b1a3d;
    --navy-mid: #1b3566;
    --frost: #e9ebee;
    --frost-shade: #cfd3d8;
    --ring-blue: #0255a3;
    --accent-blue: #33a6d7;
    --brand-navy: #0d2650;
    --icon-blue: #0692cd;
    --text-light: #ffffff;
  }
  * { margin: 0; padding: 0; box-sizing: border-box; }
  html, body {
    width: 1200px; height: 970px; overflow: hidden;
    background: var(--page-bg);
    font-family: "Jost", "Futura", sans-serif;
  }
  .business-card {
    position: absolute; left: 100px; top: 200px;
    width: 1000px; height: 570px;
    border-radius: 22px; overflow: hidden;
    box-shadow: 0 12px 40px rgba(20, 30, 50, 0.18);
  }
  .card-art { position: absolute; inset: 0; }
  .contact-block {
    position: absolute; left: 63px; top: 128px;
    color: var(--text-light);
  }
  .person-name {
    font-weight: 600; font-size: 33px; letter-spacing: 0.5px;
    color: var(--accent-blue); line-height: 1.1;
  }
  .person-title {
    font-size: 25px; font-weight: 400; letter-spacing: 0.5px;
    margin-top: 4px;
  }
  .address { font-size: 23px; line-height: 34px; margin-top: 18px; }
  .contact-list { list-style: none; margin-top: 18px; }
  .contact-list li {
    display: flex; align-items: center; gap: 12px;
    font-size: 22px; line-height: 34px;
  }
  .contact-icon { width: 26px; height: 26px; flex: none; }
  .brand-name {
    position: absolute; left: 470px; width: 510px; top: 248px;
    text-align: center;
    font-weight: 600; font-size: 76px; letter-spacing: 1px;
    color: var(--brand-navy); line-height: 1;
  }
</style>
</head>
<body>
  <div class="business-card">
    <svg class="card-art" width="1000" height="570" viewBox="0 0 1000 570" aria-hidden="true">
      <defs>
        <clipPath id="card-shape"><rect width="1000" height="570" rx="22"/></clipPath>
        <linearGradient id="panel-gradient" x1="0" y1="0" x2="1" y2="1">
          <stop offset="0" stop-color="var(--navy-mid)"/>
          <stop offset="0.55" stop-color="var(--navy-deep)"/>
          <stop offset="1" stop-color="var(--navy-mid)"/>
        </linearGradient>
        <radialGradient id="frost-gradient" cx="0.6" cy="0.4" r="0.7">
          <stop offset="0" stop-color="var(--frost)"/>
          <stop offset="1" stop-color="var(--frost-shade)"/>
        </radialGradient>
      </defs>
      <g clip-path="url(#card-shape)">
        <rect width="1000" height="570" fill="url(#frost-gradient)"/>
        <path d="M0 0 H634 A296 296 0 0 0 641 570 H0 Z" fill="url(#panel-gradient)"/>
        <path d="M634 0 A296 296 0 0 0 641 570" fill="none" stroke="var(--ring-blue)" stroke-width="5"/>
        <path d="M640 6 A290 290 0 0 0 646 564" fill="none" stroke="#ffffff" stroke-opacity="0.35" stroke-width="1.5"/>
      </g>
    </svg>

    <div class="contact-block">
      <h1 class="person-name">MARA ELLISON</h1>
      <p class="person-title">CEO/FOUNDER</p>
      <p class="address">412 Wattle Crescent<br>Marrickville, Sydney 2204</p>
      <ul class="contact-list">
        <li>
          <svg class="contact-icon" viewBox="0 0 26 26"><circle cx="13" cy="13" r="13" fill="var(--icon-blue)"/><path d="M8.5 7.5c1-.8 2-.6 2.6.6l.8 1.6c.3.7.1 1.3-.5 1.8l-.6.4c.6 1.6 1.7 2.8 3.3 3.5l.5-.6c.5-.6 1.2-.7 1.8-.4l1.6.9c1.1.6 1.2 1.6.4 2.5-1.4 1.6-3.5 1.3-5.8-.3-2.3-1.700-4.2-4.200-4.6-6.300-.2-1.4.1-2.9.5-3.700z" fill="#fff"/></svg>
          612 480 3917
        </li>
        <li>
          <svg class="contact-icon" viewBox="0 0 26 26"><circle cx="13" cy="13" r="13" fill="var(--icon-blue)"/><rect x="9" y="6" width="8" height="14" rx="1.5" fill="none" stroke="#fff" stroke-width="1.6"/><circle cx="13" cy="17.5" r="0.9" fill="#fff"/></svg>
          614 925 7063
        </li>
        <li>
          <svg class="contact-icon" viewBox="0 0 26 26"><circle cx="13" cy="13" r="13" fill="var(--icon-blue)"/><rect x="7" y="8.5" width="12" height="9" rx="1" fill="none" stroke="#fff" stroke-width="1.5"/><path d="M7.5 9.2 13 13.4l5.5-4.2" fill="none" stroke="#fff" stroke-width="1.5"/></svg>
          mara@halvora.com
        </li>
        <li>
          <svg class="contact-icon" viewBox="0 0 26 26"><circle cx="13" cy="13" r="13" fill="var(--icon-blue)"/><circle cx="13" cy="13" r="6" fill="none" stroke="#fff" stroke-width="1.5"/><ellipse cx="13" cy="13" rx="2.6" ry="6" fill="none" stroke="#fff" stroke-width="1.2"/><path d="M7 13h12" stroke="#fff" stroke-width="1.2"/></svg>
          www.halvora.com
        </li>
      </ul>
    </div>

    <p class="brand-name">HALVORA</p>
  </div>
</body>
</html>
```